Label for packaging - front and back

Hello,
We are looking for a fresh design based off of the current one we have. We need something fresh simple and eye catching. Company is TidewellGreens.com I am including current packaging and also a trim fold fliers we had made.
TG Brochure is what we could use as design inspiration perhaps?
Updates
PLEASE replace super food with " Beyond Super Food". somewhere on the label. In addition, please include website name on front.
Target Market(s)
Nutrition, athletes, anyone who wants to improve health
Look and feel
Each slider illustrates characteristics of the customer's brand and the style your logo design should communicate.

```html
<!DOCTYPE html>
<html lang="en">
<head>
<meta charset="utf-8">
<title>Tidewell Greens – Spirulina Platensis Label</title>
<link rel="stylesheet" href="https://fonts.googleapis.com/css2?family=Montserrat:wght@300;400;800&family=Raleway:wght@300;400;500;700;800&family=Oswald:wght@500&family=Allura&display=swap">
<style>
  :root {
    --green: #47a84f;
    --teal: #3fb0cf;
    --navy: #16233f;
    --grey-text: #8f9092;
    --grey-light: #c6c6c6;
    --grey-bar: #bdbec1;
    --white: #ffffff;
  }
  * { margin: 0; padding: 0; box-sizing: border-box; }
  html, body { width: 839px; height: 1200px; overflow: hidden; background: var(--white); }
  .label {
    position: relative; width: 839px; height: 1200px; overflow: hidden;
    background: var(--white); font-family: "Raleway", sans-serif; color: var(--navy);
  }

  /* Brand */
  .brand-mark {
    position: absolute; left: 70px; top: 92px; width: 92px; height: 92px;
    border-radius: 50%; background: linear-gradient(135deg, var(--green), var(--teal));
  }
  .brand-name { position: absolute; left: 194px; top: 104px; font-family: "Raleway", sans-serif; font-weight: 500; color: var(--navy); line-height: 1; }
  .brand-name .line-1 { display: block; font-size: 37px; letter-spacing: 3px; }
  .brand-name .line-2 { display: block; font-size: 37px; letter-spacing: 3px; margin-top: 12px; }

  /* Title band */
  .title-band {
    position: absolute; left: 0; top: 258px; width: 839px; height: 215px;
    background: linear-gradient(90deg, var(--green) 0%, #45ae8f 45%, var(--teal) 100%);
  }
  .product-title { position: absolute; left: 194px; top: 281px; font-family: "Montserrat", sans-serif; line-height: 1; }
  .product-title .species { display: block; font-weight: 800; font-size: 92px; color: var(--white); letter-spacing: -1px; }
  .product-title .variety { display: block; font-weight: 300; font-size: 66px; color: var(--navy); margin-top: 6px; letter-spacing: 1px; }

  /* Tagline */
  .tagline { position: absolute; left: 80px; top: 583px; width: 290px; text-align: center; }
  .tagline .nutrient { display: block; font-family: "Oswald", sans-serif; font-weight: 500; font-size: 22px; color: var(--green); margin-left: 26px; }
  .tagline .beyond { display: block; font-family: "Allura", cursive; font-size: 58px; color: var(--navy); line-height: 0.8; margin-top: -2px; margin-left: -12px; }
  .tagline .superfood { display: block; font-family: "Montserrat", sans-serif; font-weight: 800; font-size: 38px; color: var(--grey-light); letter-spacing: 1px; margin-top: 4px; }
  .tagline-rule { position: absolute; left: 178px; top: 702px; width: 91px; height: 7px; background: linear-gradient(90deg, var(--green), var(--teal)); }

  /* Product photo area */
  .product-photo {
    position: absolute; left: 30px; top: 730px; width: 410px; height: 258px;
    background: radial-gradient(ellipse at 45% 50%, #1f6b56 0%, #2a7d62 35%, rgba(60,140,110,0.35) 65%, rgba(255,255,255,0) 78%);
  }

  .net-weight { position: absolute; left: 150px; top: 995px; width: 147px; text-align: center; }
  .net-weight .caption { display: block; font-size: 14px; font-weight: 500; color: var(--navy); }
  .net-weight .amount { display: block; font-size: 28px; font-weight: 800; color: var(--grey-light); margin-top: 4px; }

  /* Benefits */
  .benefit { position: absolute; }
  .benefit .icon {
    position: absolute; width: 72px; height: 72px; border-radius: 50%; background: var(--green);
    display: flex; align-items: center; justify-content: center;
  }
  .benefit .text { position: absolute; font-size: 17.5px; font-weight: 500; line-height: 22px; color: var(--navy); white-space: nowrap; }

  .benefit-zinc .icon { left: 392px; top: 599px; width: 70px; height: 70px; }
  .benefit-zinc .text { left: 477px; top: 597px; }
  .benefit-vitamins .icon { left: 442px; top: 699px; }
  .benefit-vitamins .text { left: 528px; top: 701px; }
  .benefit-chlorophyll .icon { left: 451px; top: 803px; }
  .benefit-chlorophyll .text { left: 535px; top: 830px; }
  .benefit-antioxidants .icon { left: 406px; top: 913px; }
  .benefit-antioxidants .text { left: 494px; top: 920px; }

  .freeze-note { position: absolute; left: 457px; top: 1088px; font-size: 19px; font-weight: 500; color: var(--grey-text); white-space: nowrap; }

  /* Bottom bar */
  .highlights {
    position: absolute; left: 0; top: 1119px; width: 839px; height: 81px; background: var(--grey-bar);
  }
  .highlight { position: absolute; top: 24px; display: flex; align-items: center; gap: 12px; white-space: nowrap; }
  .highlight svg { width: 32px; height: 32px; }
  .highlight .label-strong { font-size: 23px; font-weight: 800; color: var(--navy); }
  .highlight .label-light { font-size: 19px; font-weight: 300; color: var(--navy); margin-left: 4px; }
  .highlight-protein { left: 44px; }
  .highlight-amino { left: 312px; }
  .highlight-vitamins { left: 636px; }
</style>
</head>
<body>
<main class="label">

  <div class="brand-mark"></div>
  <div class="brand-name">
    <span class="line-1">TIDEWELL</span>
    <span class="line-2">GREENS</span>
  </div>

  <div class="title-band"></div>
  <h1 class="product-title">
    <span class="species">SPIRULINA</span>
    <span class="variety">PLATENSIS</span>
  </h1>

  <div class="tagline">
    <span class="nutrient">Nutrient Rich</span>
    <span class="beyond">beyond</span>
    <span class="superfood">SUPERFOOD</span>
  </div>
  <div class="tagline-rule"></div>

  <div class="product-photo" role="img" aria-label="Two glasses of green spirulina drink beside a heap of spirulina powder"></div>

  <div class="net-weight">
    <span class="caption">Net Weight</span>
    <span class="amount">120g</span>
  </div>

  <div class="benefit benefit-zinc">
    <div class="icon">
      <svg width="40" height="40" viewBox="0 0 40 40" fill="none" stroke="#fff" stroke-width="2" stroke-linecap="round" stroke-linejoin="round">
        <path d="M6 32 C4 24 8 14 14 8 L19 7 L20 11 L16 13 L15 20 C19 17 26 17 31 22 C35 27 31 33 25 33 Z"/>
        <path d="M14 27 C17 24 21 24 24 27"/>
      </svg>
    </div>
    <p class="text">Excellent source of<br>Zinc to boost your<br>immune system</p>
  </div>

  <div class="benefit benefit-vitamins">
    <div class="icon">
      <svg width="44" height="44" viewBox="0 0 44 44" fill="none" stroke="#fff" stroke-width="2" stroke-linecap="round">
        <circle cx="20" cy="9" r="4"/>
        <circle cx="33" cy="19" r="4"/>
        <circle cx="20" cy="24" r="3"/>
        <circle cx="9" cy="35" r="5"/>
        <circle cx="32" cy="34" r="4"/>
        <line x1="20" y1="13" x2="20" y2="21"/>
        <line x1="23" y1="23" x2="29" y2="20"/>
        <line x1="18" y1="26" x2="12" y2="31"/>
        <line x1="22" y1="26" x2="29" y2="31"/>
      </svg>
    </div>
    <p class="text">Vitamins B1, B2, B3,<br>B5, B6, B7, B8, B9,<br>C, D, E and K</p>
  </div>

  <div class="benefit benefit-chlorophyll">
    <div class="icon">
      <svg width="40" height="40" viewBox="0 0 40 40" fill="none" stroke="#fff" stroke-width="2" stroke-linecap="round" stroke-linejoin="round">
        <path d="M12 30 C6 20 14 8 32 6 C34 22 26 32 12 30 Z"/>
        <path d="M4 36 L24 16"/>
      </svg>
    </div>
    <p class="text">Chlorophyll</p>
  </div>

  <div class="benefit benefit-antioxidants">
    <div class="icon">
      <svg width="44" height="44" viewBox="0 0 44 44" fill="none" stroke="#fff" stroke-width="2" stroke-linecap="round" stroke-linejoin="round">
        <path d="M22 38 L7 23 C2 18 4 8 12 8 C16 8 19 10 22 14 C25 10 28 8 32 8 C40 8 42 18 37 23 Z"/>
        <path d="M6 22 L15 22 L18 17 L22 29 L25 22 L38 22"/>
      </svg>
    </div>
    <p class="text">Powerful source of<br>Antooxidants<br>and protein</p>
  </div>

  <p class="freeze-note">Freeze dried to preserve all nutirition</p>

  <div class="highlights">
    <div class="highlight highlight-protein">
      <svg viewBox="0 0 32 32" fill="none" stroke="#16233f" stroke-width="3" stroke-linecap="round" stroke-linejoin="round"><path d="M27 12 A12 12 0 1 1 20 5"/><path d="M10 15 L15 21 L28 6"/></svg>
      <span><span class="label-strong">Protein</span><span class="label-light">70%</span></span>
    </div>
    <div class="highlight highlight-amino">
      <svg viewBox="0 0 32 32" fill="none" stroke="#16233f" stroke-width="3" stroke-linecap="round" stroke-linejoin="round"><path d="M27 12 A12 12 0 1 1 20 5"/><path d="M10 15 L15 21 L28 6"/></svg>
      <span><span class="label-strong">Amino Acids</span><span class="label-light">19</span></span>
    </div>
    <div class="highlight highlight-vitamins">
      <svg viewBox="0 0 32 32" fill="none" stroke="#16233f" stroke-width="3" stroke-linecap="round" stroke-linejoin="round"><path d="M27 12 A12 12 0 1 1 20 5"/><path d="M10 15 L15 21 L28 6"/></svg>
      <span class="label-strong">Vitamins</span>
    </div>
  </div>

</main>
</body>
</html>
```